Super Greens Label for Supplement Bottle

We want to design a front label for a health supplement bottle. The product is called Meadow Crunch Chews™. This will be a new product so there is no current website for the product. The focus is on supergreens that taste great and deliver support for energy, digestion, and immune defense.
We want it to be modern, vibrant and appealing.
Bottle size: standard size supplement CLEAR bottle size, with white child resistant cap and the label panel dimensions are 3” x 7”. The label should be primarily white and green, with a touch of red; (see color palettes)/it can also ONLY be white and green. See samples attached.
We are only focused on the front of the bottle design, not on the back, but leave space for the supplement panel and other text on the back.
So the text for the front of the bottle is:
RT Halvorsen's
Meadow Crunch Chews™
Super Greens Blend for:
Energy, Digestion, and Immune Support*
60 Gummies | Dietary Supplement
Raspberry Flavor Gummies
Off to side of the label:
Non-GMO
Vegan Friendly
Plant-Based
Gelatin Free
Colors
Designer to choose colors to be used in the design.
Look and feel
Each slider illustrates characteristics of the customer's brand and the style your logo design should communicate.

```html
<!DOCTYPE html>
<html lang="en">
<head>
<meta charset="utf-8">
<title>Meadow Crunch Chews – Front Label</title>
<link href="https://fonts.googleapis.com/css2?family=Quicksand:wght@500;600;700&display=swap" rel="stylesheet">
<style>
  :root {
    --green-deep: #0f743c;
    --green-mid: #1f8a3e;
    --green-lime: #8fb43a;
    --red: #d21f27;
    --white: #ffffff;
    --canvas: #ffffff;
  }
  * { margin: 0; padding: 0; box-sizing: border-box; }
  html, body { width: 1200px; height: 1000px; overflow: hidden; background: var(--canvas); }
  body { font-family: "Quicksand", "Segoe UI", sans-serif; color: var(--white); position: relative; }

  .label {
    position: absolute; left: 76px; top: 275px;
    width: 1049px; height: 450px;
    background: var(--green-deep);
    overflow: hidden;
  }
  .front-panel {
    position: absolute; left: 0; top: 0; width: 440px; height: 450px;
    background:
      radial-gradient(ellipse 320px 220px at 110px 430px, rgba(143,180,58,0.85), rgba(143,180,58,0) 70%),
      radial-gradient(ellipse 300px 200px at 300px 330px, rgba(90,160,50,0.5), rgba(90,160,50,0) 70%),
      var(--green-deep);
  }
  .tagline {
    position: absolute; top: 40px; left: 0; width: 500px; text-align: center;
    font-size: 15px; font-weight: 500; line-height: 1.4;
  }
  .product-name {
    position: absolute; top: 92px; left: 0; width: 500px; text-align: center;
    font-weight: 700; line-height: 1;
  }
  .product-name .line-1 { display: block; font-size: 38px; }
  .product-name .line-2 { display: block; font-size: 56px; margin-top: 4px; }

  .count-pill {
    position: absolute; left: 0; top: 208px; width: 178px; height: 82px;
    border-radius: 0 41px 41px 0;
    background: linear-gradient(90deg, var(--green-lime), #4f9a3a);
  }
  .count-number {
    position: absolute; left: 110px; top: 225px; font-size: 40px; font-weight: 700;
  }
  .count-text { position: absolute; left: 183px; top: 224px; line-height: 1.1; }
  .count-text .unit { display: block; font-size: 24px; font-weight: 700; }
  .count-text .kind { display: block; font-size: 15px; font-weight: 700; margin-top: 3px; }

  .fruit-art {
    position: absolute; left: 140px; top: 278px; width: 190px; height: 118px;
    border-radius: 50% 50% 40% 40%;
    background: radial-gradient(circle at 50% 55%, #e0303f, #b81c2c 60%, rgba(184,28,44,0) 75%);
  }
  .flavor-band {
    position: absolute; left: 0; top: 388px; width: 315px; height: 35px;
    border-radius: 0 18px 18px 0; background: var(--red);
    display: flex; align-items: center; justify-content: flex-end; padding-right: 30px;
    font-size: 16px; font-weight: 700;
  }

  .claims-strip {
    position: absolute; left: 440px; top: 0; width: 145px; height: 450px;
    background: linear-gradient(180deg, var(--green-lime), #3e8f3f 60%, #1d7f3c);
    box-shadow: -4px 0 10px rgba(0,0,0,0.18), 4px 0 10px rgba(0,0,0,0.18);
  }
  .claim {
    position: absolute; left: 0; width: 145px; text-align: center;
    font-size: 12px; font-weight: 600;
  }
  .claim svg { display: block; margin: 0 auto 8px; }
</style>
</head>
<body>
  <div class="label">
    <section class="front-panel">
      <p class="tagline">Super Greens Blend for:<br>Energy, Digestion, Immune Support</p>
      <h1 class="product-name"><span class="line-1">Meadow Crunch</span><span class="line-2">Chews™</span></h1>
      <div class="count-pill"></div>
      <span class="count-number">60</span>
      <p class="count-text"><span class="unit">Gummies</span><span class="kind">| Dietary Supplement</span></p>
      <div class="fruit-art" role="img" aria-label="Cluster of fresh raspberries with green leaves"></div>
      <div class="flavor-band">Raspberry Flavor</div>
    </section>

    <aside class="claims-strip">
      <div class="claim" style="top:40px">
        <svg width="50" height="50" viewBox="0 0 50 50" fill="none" stroke="#fff" stroke-width="3" stroke-linecap="round">
          <circle cx="25" cy="25" r="22"/>
          <path d="M10 10 L40 40"/>
          <path d="M19 12 C31 20 19 30 31 38"/>
          <path d="M31 12 C19 20 31 30 19 38"/>
        </svg>
        NON GMO
      </div>
      <div class="claim" style="top:135px">
        <svg width="50" height="50" viewBox="0 0 50 50" fill="#fff">
          <path d="M10 14 h7 l7 24 l7 -24 h5 l-10 32 h-6 z"/>
          <path d="M30 18 C30 6 40 2 48 2 C48 12 42 18 32 20 z"/>
        </svg>
        VEGAN FRIENDLY
      </div>
      <div class="claim" style="top:235px">
        <svg width="60" height="50" viewBox="0 0 60 50" fill="#fff">
          <path d="M30 48 C30 34 32 26 38 20 L40 22 C34 28 32 36 32 48 z"/>
          <path d="M36 22 C38 8 48 4 58 4 C56 16 48 24 36 22 z"/>
          <path d="M28 30 C20 32 8 28 2 18 C14 14 24 18 28 30 z"/>
        </svg>
        PLANT BASED
      </div>
      <div class="claim" style="top:335px">
        <svg width="50" height="50" viewBox="0 0 50 50" fill="none" stroke="#fff" stroke-width="3" stroke-linejoin="round">
          <path d="M12 34 L14 8 Q25 2 36 8 L38 34 Z"/>
          <path d="M20 8 L20 34 M30 8 L30 34"/>
          <path d="M6 34 H44 M25 34 V44 M14 46 H36"/>
        </svg>
        GELATIN FREE
      </div>
    </aside>
  </div>
</body>
</html>
```